Business card for medical clinic

I need an upmarket, modern medical/health business card for my clinic

Contact Information for Business Card

name, address, email, qr code

```html
<!DOCTYPE html>
<html lang="en">
<head>
<meta charset="utf-8">
<title>Meridia Care Clinic – Business Card</title>
<link rel="stylesheet" href="https://fonts.googleapis.com/css2?family=Montserrat:wght@400;500;700&display=swap">
<style>
  :root {
    --navy: #1b2540;
    --navy-deep: #121a30;
    --pattern-blue: #3a57b8;
    --brand-blue: #2a7fbf;
    --sky: #22a8e2;
    --ink: #1a1a1a;
    --paper: #ffffff;
    --backdrop: #e9ebef;
  }
  * { box-sizing: border-box; margin: 0; padding: 0; }
  html, body { width: 1200px; height: 931px; overflow: hidden; }
  body {
    background: var(--backdrop);
    font-family: "Montserrat", sans-serif;
    position: relative;
  }
  .card {
    position: absolute;
    left: 290px;
    width: 620px;
    height: 354px;
    border-radius: 18px;
    overflow: hidden;
    box-shadow: 0 6px 18px rgba(0,0,0,.18);
  }
  .card-back { top: 61px; background: var(--navy); }
  .card-front { top: 516px; background: var(--paper); }

  .back-pattern {
    position: absolute; inset: 0;
    background: radial-gradient(ellipse at 15% 30%, rgba(58,87,184,.35), transparent 55%), var(--navy);
  }
  .back-brand {
    position: absolute; left: 0; right: 0; top: 160px;
    display: flex; align-items: center; justify-content: center; gap: 12px;
    color: var(--paper); font-weight: 500; font-size: 22px; letter-spacing: 3px;
  }
  .brand-dot { width: 14px; height: 14px; border-radius: 50%; background: currentColor; }

  .front-brand {
    position: absolute; right: 56px; top: 66px;
    display: flex; align-items: center; gap: 12px;
    color: var(--brand-blue); font-weight: 500; font-size: 24px; letter-spacing: 3px;
  }
  .holder { position: absolute; left: 40px; top: 150px; }
  .holder-name { color: var(--brand-blue); font-weight: 700; font-size: 28px; line-height: 1; }
  .holder-role { color: var(--ink); font-size: 14px; margin-top: 6px; }
  .divider { position: absolute; left: 40px; right: 30px; top: 208px; height: 1.5px; background: var(--sky); }

  .contacts { position: absolute; left: 40px; top: 226px; list-style: none; }
  .contacts li {
    display: flex; align-items: center; gap: 12px;
    font-size: 15px; color: var(--ink); height: 28px;
  }
  .contacts svg { width: 15px; height: 15px; fill: var(--sky); }

  .address {
    position: absolute; right: 40px; top: 232px;
    text-align: right; font-size: 14px; line-height: 1.4; color: var(--ink);
  }
  .front-band { position: absolute; left: 0; bottom: 0; width: 100%; height: 20px; }
</style>
</head>
<body>
  <section class="card card-back">
    <div class="back-pattern" role="img" aria-label="Repeating tonal ring pattern across the navy back"></div>
    <div class="back-brand"><span class="brand-dot"></span>MERIDIA CARE CLINIC</div>
  </section>

  <section class="card card-front">
    <div class="front-brand"><span class="brand-dot"></span>MERIDIA CARE CLINIC</div>

    <div class="holder">
      <div class="holder-name">Daniel Reyes</div>
      <div class="holder-role">Managing Director</div>
    </div>
    <div class="divider"></div>

    <ul class="contacts">
      <li>
        <svg viewBox="0 0 24 24"><path d="M6.6 10.8a15 15 0 0 0 6.6 6.6l2.2-2.2a1 1 0 0 1 1-.25 11.4 11.4 0 0 0 3.6.57 1 1 0 0 1 1 1V20a1 1 0 0 1-1 1A17 17 0 0 1 3 4a1 1 0 0 1 1-1h3.5a1 1 0 0 1 1 1c0 1.25.2 2.45.57 3.57a1 1 0 0 1-.25 1z"/></svg>
        555.204.7316
      </li>
      <li>
        <svg viewBox="0 0 24 24"><path d="M2 5h20v14H2z M2 5l10 8 10-8" stroke="#fff" stroke-width="1.5"/></svg>
        hello@meridiacare.com
      </li>
      <li>
        <svg viewBox="0 0 24 24"><circle cx="12" cy="12" r="10"/></svg>
        www.meridiacare.com
      </li>
    </ul>

    <div class="address">48 Cedar Hollow Lane<br>Ridgeford, MS 39200</div>

    <svg class="front-band" viewBox="0 0 620 20" preserveAspectRatio="none">
      <rect width="620" height="20" fill="var(--navy-deep)"/>
      <polygon points="512,0 620,0 620,20 506,20" fill="var(--sky)"/>
      <polygon points="505,0 510,0 504,20 499,20" fill="#fff"/>
    </svg>
  </section>
</body>
</html>
```